Business Card Design

We provide services doing multiple jobs in the construction industry.Please note: The company name needs to be ROCK SOLID BUILDING SERVICESAttached logo was an example of what we wanted. Can you change up the colors?

Industry/Entity Type

Construction

Contact Information for Business Card

ROCK SOLID BUILDING SERVICES5401 HUDSON BEND RDAUSTIN, TX 78734(512)243-6854ROCKSOLIDBUILDINGSERVICES@GMAIL.COM

```html
<!DOCTYPE html>
<html lang="en">
<head>
<meta charset="utf-8">
<title>Pearlwood Framing Works – Business Card</title>
<link rel="stylesheet" href="https://fonts.googleapis.com/css2?family=Exo+2:wght@400;600&display=swap">
<style>
  :root {
    --navy: #24226e;
    --navy-deep: #1a1852;
    --white: #ffffff;
    --paper: #f2f2f4;
    --silver: #b9bcc4;
    --backdrop: #e7e5e1;
    --ink: #24226e;
  }
  * { box-sizing: border-box; margin: 0; padding: 0; }
  html, body { width: 1200px; height: 828px; overflow: hidden; }
  body {
    background: var(--backdrop);
    font-family: "Exo 2", sans-serif;
    position: relative;
  }
  .card {
    position: absolute;
    width: 525px;
    height: 300px;
    top: 264px;
    overflow: hidden;
    box-shadow: 0 6px 18px rgba(0,0,0,.18);
  }
  .card-front { left: 50px; }
  .card-back  { left: 625px; }
  .card svg.shapes { position: absolute; inset: 0; }

  .brand {
    position: absolute;
    display: flex;
    align-items: center;
    gap: 10px;
    color: var(--ink);
    font-weight: 600;
    letter-spacing: .06em;
    text-transform: uppercase;
    white-space: nowrap;
  }
  .brand-mark {
    width: 16px; height: 16px;
    background: var(--ink);
    flex: none;
  }
  .card-front .brand { left: 0; right: 0; top: 74px; justify-content: center; font-size: 20px; }
  .card-back .brand { left: 22px; top: 206px; font-size: 15px; }

  .website-line {
    position: absolute;
    left: 0; right: 0; bottom: 34px;
    text-align: center;
    color: var(--white);
    font-size: 14px;
    letter-spacing: .32em;
  }

  .contact {
    position: absolute;
    right: 24px; top: 26px;
    text-align: right;
    color: var(--white);
  }
  .contact .person { font-size: 19px; letter-spacing: .08em; font-weight: 600; }
  .contact .role { font-size: 12px; margin-top: 2px; letter-spacing: .04em; }
  .contact .address { font-size: 12px; margin-top: 26px; line-height: 1.45; }
  .contact ul { list-style: none; margin-top: 14px; font-size: 12px; line-height: 1.9; }
  .contact li { display: flex; justify-content: flex-end; align-items: center; gap: 8px; }
  .contact li svg { width: 11px; height: 11px; fill: var(--white); flex: none; }
</style>
</head>
<body>

<section class="card card-front" aria-label="Card front">
  <svg class="shapes" viewBox="0 0 525 300" preserveAspectRatio="none">
    <defs>
      <linearGradient id="frontNavy" x1="0" y1="0" x2="1" y2="1">
        <stop offset="0" stop-color="#2d2b82"/>
        <stop offset="1" stop-color="#1a1852"/>
      </linearGradient>
      <linearGradient id="paperShade" x1="0" y1="0" x2="0" y2="1">
        <stop offset="0" stop-color="#ffffff"/>
        <stop offset="1" stop-color="#e9e9ee"/>
      </linearGradient>
    </defs>
    <rect width="525" height="300" fill="url(#paperShade)"/>
    <path d="M0,170 C170,214 380,170 525,20 L525,300 L0,300 Z" fill="#cfd1d7"/>
    <path d="M0,182 C175,224 385,182 525,34 L525,300 L0,300 Z" fill="url(#frontNavy)"/>
  </svg>
  <div class="brand"><span class="brand-mark"></span>Pearlwood Framing Works</div>
  <p class="website-line">www.pearlwoodframing.example</p>
</section>

<section class="card card-back" aria-label="Card back">
  <svg class="shapes" viewBox="0 0 525 300" preserveAspectRatio="none">
    <defs>
      <linearGradient id="backNavy" x1="0" y1="0" x2="1" y2="1">
        <stop offset="0" stop-color="#2d2b82"/>
        <stop offset="1" stop-color="#1a1852"/>
      </linearGradient>
    </defs>
    <rect width="525" height="300" fill="url(#backNavy)"/>
    <path d="M0,118 C150,112 300,170 350,300 L0,300 Z" fill="#c3c6cd"/>
    <path d="M0,128 C145,124 288,178 336,300 L0,300 Z" fill="#f3f3f6"/>
  </svg>
  <div class="brand"><span class="brand-mark"></span>Pearlwood Framing Works</div>

  <div class="contact">
    <p class="person">DANIEL MERCER</p>
    <p class="role">Managing Director</p>
    <p class="address">7732 Fernglen Pass Ln<br>Suite 4 TX</p>
    <ul>
      <li>(512)555-0193
        <svg viewBox="0 0 24 24"><path d="M6.6 10.8a15 15 0 006.6 6.6l2.2-2.2c.3-.3.7-.4 1-.2 1.1.4 2.3.6 3.6.6.6 0 1 .4 1 1V20c0 .6-.4 1-1 1A17 17 0 013 4c0-.6.4-1 1-1h3.5c.6 0 1 .4 1 1 0 1.3.2 2.5.6 3.6.1.3 0 .7-.2 1z"/></svg></li>
      <li>(512)555-0194
        <svg viewBox="0 0 24 24"><path d="M7 1h10a2 2 0 012 2v18a2 2 0 01-2 2H7a2 2 0 01-2-2V3a2 2 0 012-2zm0 3v14h10V4zm5 15.5a1 1 0 100 2 1 1 0 000-2z"/></svg></li>
      <li>(512)555-0195
        <svg viewBox="0 0 24 24"><path d="M6 2h9l4 4v5H6zm-2 11h16a2 2 0 012 2v7H2v-7a2 2 0 012-2zm3 3v2h4v-2z"/></svg></li>
      <li>hello@pearlwood.example
        <svg viewBox="0 0 24 24"><path d="M2 5h20v14H2zm2 2v.5l8 5 8-5V7z"/></svg></li>
      <li>www.pearlwoodframing.example
        <svg viewBox="0 0 24 24"><path d="M12 2a10 10 0 110 20 10 10 0 010-20zm0 2c-1 1.5-1.8 3.3-2 5h4c-.2-1.7-1-3.5-2-5zM4.3 9h3.7c.1-1.8.6-3.5 1.4-4.8A8 8 0 004.3 9zm15.4 0a8 8 0 00-5.1-4.8c.8 1.3 1.3 3 1.4 4.8zM4.3 15a8 8 0 005.1 4.8c-.8-1.3-1.3-3-1.4-4.8zm5.7 0c.2 1.7 1 3.5 2 5 1-1.5 1.8-3.3 2-5zm6 0c-.1 1.8-.6 3.5-1.4 4.8a8 8 0 005.1-4.8zM4 11v2h4v-2zm6 0v2h4v-2zm6 0v2h4v-2z"/></svg></li>
    </ul>
  </div>
</section>

</body>
</html>
```